Design a large parking banner – mandatory ticket validation in the shop

Banner Size:
548 cm (width) x 154 cm (height)
Note: The banner will be placed in a metal frame at our parking lot entrance, fully visible to every incoming truck driver. The message must be easy to read from a distance.
Goal of the Banner:
To inform all truck drivers that they must validate their entry ticket inside the shop, even if they are parking for a short time.
The message must be displayed in multiple languages for international drivers.
Mandatory Content:
Main message – in multiple languages (clearly separated or stacked):
Dutch (NL): Vergeet je ticket niet te valideren in de shop – verplicht, ook bij kort parkeren!
French (FR): N'oubliez pas de valider votre ticket à la boutique – obligatoire, même pour un court arrêt !
English (EN): Don't forget to validate your entry ticket in the shop – mandatory, even for short stops!
German (DE): Vergessen Sie nicht, Ihr Einfahrticket im Shop zu entwerten – Pflicht, auch bei kurzem Parken!
Polish (PL): Nie zapomnij zatwierdzić biletu w sklepie – obowiązkowe, nawet przy krótkim postoju!
Romanian (RO): Nu uitați să validați biletul în magazin – obligatoriu, chiar și pentru opriri scurte!
You can include more languages if space allows, but these are essential.
Opening Hours Block (in one section below):
Shop Opening Hours
Mon – Fri: 05:30 – 22:00
Sat & Sun: 08:00 – 22:00
Style & Branding:
The design must match the visual identity of Haulport 41Ter
Please refer to the attached photos of existing parking signage for guidance on colors, typography, and layout style
Our logo (attached) must be clearly visible and professionally integrated
Feel free to use icons or pictograms to visually support the message (e.g., ticket, truck, arrow)
Readability is key – large, bold text and high contrast colors that are visible from a distance
Target Audience:
International truck drivers – people who need fast, clear communication. Not everyone speaks the local language, so visual clarity and multilingual messaging are critical.
File Requirements:
Print-ready file (PDF or EPS) – 300 dpi at 1:10 scale
Include 5 cm bleed on all sides
Provide open source files if possible (AI or PSD)

```html
<!DOCTYPE html>
<html lang="en">
<head>
<meta charset="utf-8">
<title>Parking banner – ticket validation</title>
<link href="https://fonts.googleapis.com/css2?family=Montserrat:ital,wght@1,700&family=Saira+Condensed:ital,wght@0,800;1,800&display=swap" rel="stylesheet">
<style>
  :root {
    --page: #e8e8e8;
    --navy-light: #2c3a82;
    --navy-dark: #0b1350;
    --rule: #3a6cc4;
    --band: #1b80c6;
    --white: #ffffff;
    --red: #d8202a;
    --ink: #15204f;
  }
  * { margin: 0; padding: 0; box-sizing: border-box; }
  html, body { width: 1200px; height: 408px; overflow: hidden; background: var(--page); }
  .banner {
    position: absolute; left: 68px; top: 56px;
    width: 1064px; height: 294px; overflow: hidden;
  }
  .messages {
    position: absolute; left: 0; top: 0; width: 100%; height: 192px;
    background: linear-gradient(90deg, var(--navy-light), var(--navy-dark));
    padding-top: 3px;
  }
  .message {
    height: 28px; line-height: 28px; text-align: center;
    font-family: "Montserrat", sans-serif; font-style: italic; font-weight: 700;
    font-size: 16.6px; color: var(--white); white-space: nowrap;
    border-bottom: 1px solid var(--rule);
  }
  .message:last-child { border-bottom: none; }
  .message .must { color: var(--red); }
  .hours-band {
    position: absolute; left: 0; top: 192px; width: 100%; height: 102px;
    background: var(--band);
  }
  .hours-title {
    position: absolute; left: 48px; top: 6px;
    font-family: "Saira Condensed", sans-serif; font-style: italic; font-weight: 800;
    font-size: 40px; line-height: 38px; color: var(--white); text-transform: uppercase;
  }
  .hours-row { position: absolute; left: 330px; height: 38px; }
  .hours-row.weekdays { top: 3px; }
  .hours-row.weekend { top: 46px; }
  .hours-day, .hours-time {
    position: absolute; top: 0; height: 38px; line-height: 40px;
    font-family: "Saira Condensed", sans-serif; font-style: italic; font-weight: 800;
    font-size: 34px; text-align: center; transform: skewX(-12deg);
  }
  .hours-day { left: 0; width: 196px; background: var(--white); color: var(--ink); }
  .hours-time { left: 190px; width: 244px; background: var(--red); color: var(--white); }
  .hours-day span, .hours-time span { display: inline-block; transform: skewX(12deg); }
  .brand {
    position: absolute; left: 806px; top: 22px;
    display: flex; align-items: center; gap: 8px;
    font-family: "Saira Condensed", sans-serif; font-weight: 800;
    font-size: 36px; line-height: 40px; color: var(--white);
  }
  .brand-mark { width: 14px; height: 14px; background: var(--white); }
  .brand-rule {
    position: absolute; left: 796px; top: 90px; width: 118px; height: 5px;
    background: var(--red);
  }
</style>
</head>
<body>
  <div class="banner">
    <div class="messages">
      <p class="message" lang="nl">Vergeet je ticket niet te valideren in de shop – <span class="must">verplicht, ook bij kort parkeren!</span></p>
      <p class="message" lang="fr">N'oubliez pas de valider votre ticket à la boutique – <span class="must">obligatoire, même pour un court arrêt !</span></p>
      <p class="message" lang="en">Don't forget to validate your entry ticket in the shop – <span class="must">mandatory, even for short stops!</span></p>
      <p class="message" lang="de">Vergessen Sie nicht, Ihr Einfahrticket im Shop zu entwerten – <span class="must">Pflicht, auch bei kurzem Parken!</span></p>
      <p class="message" lang="pl">Nie zapomnij zatwierdzić biletu w sklepie – <span class="must">obowiązkowe, nawet przy krótkim postoju!</span></p>
      <p class="message" lang="ro">Nu uitați să validați biletul în magazin – <span class="must">obligatoriu, chiar și pentru opriri scurte!</span></p>
    </div>
    <div class="hours-band">
      <h2 class="hours-title">Shop opening<br>hours</h2>
      <div class="hours-row weekdays">
        <div class="hours-day"><span>MON — FRI:</span></div>
        <div class="hours-time"><span>05:30 — 22:00</span></div>
      </div>
      <div class="hours-row weekend">
        <div class="hours-day"><span>SAT &amp; SUN:</span></div>
        <div class="hours-time"><span>08:00 — 22:00</span></div>
      </div>
      <div class="brand"><span class="brand-mark"></span>Haulport 41Ter</div>
      <div class="brand-rule"></div>
    </div>
  </div>
</body>
</html>
```